American cannabis tech company business card design

Pavrel.com is seeking a modern, professional, and brand-aligned business card that represents our company and its core values: Mission, Story, Values, and Impact. As an innovative cannabis company, we want a business card that is not only visually appealing but also serves as a representation of who we are and what we stand for.

Project Scope: Design a double-sided business card that integrates our brand identity and core values. Incorporate our key brand elements, ensuring a sleek and contemporary aesthetic. Visually reflect our core values (Mission, Story, Values, Impact) in a way that is engaging yet professional.

Target Market(s)

Vendors, third parties,

Contact Information for Business Card

Contact details (name, title, email, phone, website, etc.)

Font styles to use
Other font styles liked:
• Caslon, Centra

Colors

Designer to choose colors to be used in the design.

Requirements
Must have
• Pavrel.com logo and branding A creative yet clean way to integrate our core values (Mission, Story, Values, Impact) Modern typography and a well-structured layout
Nice to have
• forest green, grey, white, black
Should not have
• references to marijuana, leafs, plants, or related product

```html
<!DOCTYPE html>
<html lang="en">
<head>
<meta charset="utf-8">
<title>Pavrel.com Business Card</title>
<link href="https://fonts.googleapis.com/css2?family=Poppins:wght@400;600;800&display=swap" rel="stylesheet">
<style>
  :root {
    --forest: #1f4a22;
    --forest-dark: #163a19;
    --card-white: #f4f4f4;
    --ink: #2b2b2b;
    --divider: #c9c9c9;
    --silver: #d6d6d6;
    --backdrop: #2a2a2a;
  }
  * { margin: 0; padding: 0; box-sizing: border-box; }
  html, body {
    width: 1200px;
    height: 900px;
    overflow: hidden;
    background: var(--backdrop);
    font-family: "Poppins", sans-serif;
  }
  .sheet {
    width: 1200px;
    height: 900px;
    display: flex;
    align-items: center;
    justify-content: center;
    gap: 60px;
  }
  .card {
    width: 525px;
    height: 300px;
    border-radius: 22px;
    position: relative;
    overflow: hidden;
  }
  .card--front {
    background: var(--card-white);
    display: flex;
    align-items: center;
  }
  .card--back {
    background: var(--forest);
    display: flex;
    align-items: center;
    justify-content: center;
  }
  .brand-name {
    font-family: "Poppins", sans-serif;
    font-weight: 800;
    letter-spacing: -1px;
    line-height: 1;
  }
  .card--front .brand-block {
    width: 54%;
    display: flex;
    justify-content: center;
  }
  .card--front .brand-name {
    color: var(--forest-dark);
    font-size: 52px;
  }
  .card--back .brand-name {
    color: var(--silver);
    font-size: 86px;
  }
  .divider {
    width: 1px;
    height: 190px;
    background: var(--divider);
  }
  .contact-block {
    padding-left: 26px;
    flex: 1;
  }
  .person-name {
    color: var(--forest-dark);
    font-weight: 600;
    font-size: 17px;
    letter-spacing: 0.3px;
  }
  .person-title {
    color: var(--ink);
    font-size: 12px;
    margin-bottom: 22px;
  }
  .contact-list { list-style: none; }
  .contact-item {
    display: flex;
    align-items: center;
    gap: 8px;
    color: var(--ink);
    font-size: 13px;
    margin-bottom: 8px;
  }
  .contact-item--web { color: var(--forest); }
  .contact-icon { width: 20px; height: 20px; flex: none; }
</style>
</head>
<body>
<main class="sheet">
  <section class="card card--front" aria-label="Business card front">
    <div class="brand-block">
      <span class="brand-name">Pavrel</span>
    </div>
    <div class="divider"></div>
    <div class="contact-block">
      <p class="person-name">DANIEL HART</p>
      <p class="person-title">Managing Director</p>
      <ul class="contact-list">
        <li class="contact-item">
          <svg class="contact-icon" viewBox="0 0 20 20" aria-hidden="true">
            <circle cx="10" cy="10" r="9" fill="none" stroke="#1f4a22" stroke-width="1.2"/>
            <path d="M7 5.5l1.6 0 .8 2.2-1 .9c.6 1.3 1.6 2.3 2.9 2.9l.9-1 2.2.8 0 1.6c0 .6-.5 1-1.1 1-4 -.3-7.2-3.5-7.4-7.5 0-.5.4-.9 1.1-.9z" fill="#1f4a22"/>
          </svg>
          044-555 201 347
        </li>
        <li class="contact-item">
          <svg class="contact-icon" viewBox="0 0 20 20" aria-hidden="true">
            <circle cx="10" cy="10" r="9" fill="none" stroke="#1f4a22" stroke-width="1.2"/>
            <rect x="5" y="6.5" width="10" height="7" rx="1" fill="#1f4a22"/>
            <path d="M5.3 7l4.7 3.6L14.7 7" fill="none" stroke="#f4f4f4" stroke-width="1"/>
          </svg>
          info@pavrel.com
        </li>
        <li class="contact-item contact-item--web">
          <svg class="contact-icon" viewBox="0 0 20 20" aria-hidden="true">
            <circle cx="10" cy="10" r="9" fill="none" stroke="#1f4a22" stroke-width="1.2"/>
            <circle cx="10" cy="10" r="5" fill="none" stroke="#1f4a22" stroke-width="1"/>
            <ellipse cx="10" cy="10" rx="2.2" ry="5" fill="none" stroke="#1f4a22" stroke-width="1"/>
            <path d="M5 10h10" stroke="#1f4a22" stroke-width="1"/>
          </svg>
          www.pavrel.com
        </li>
      </ul>
    </div>
  </section>

  <section class="card card--back" aria-label="Business card back">
    <span class="brand-name">Pavrel</span>
  </section>
</main>
</body>
</html>
```